Irrigation Business needs their business cards modernised and revamped

I would like to keep my current logo, colours and revamp the format of the card.

I would like the card to be clean yet important.

Im not sure if you include texture but i would like the named logo to be indented into the card etc.

show me something alive and free something thats clinical to the point yet has a feel of achievement. i would like people to go nice card.

Target Market(s)

high end clients, corporate, sports field manger, the guys that make the decisions

Industry/Entity Type

Business

Contact Information for Business Card

nformation to be included

Dean Harlow (Director)
0487305526
dean@kolvat.biz
www.kestonfieldworks.com

instagram logo
google logo
facebook logo

Colors

Designer to choose colors to be used in the design.

Requirements
Nice to have
• indentations a really nice feel to the card good texture

```html
<!DOCTYPE html>
<html lang="en">
<head>
<meta charset="utf-8">
<title>Keston Fieldworks Services – Business Card</title>
<link rel="stylesheet" href="https://fonts.googleapis.com/css2?family=Archivo:wght@700&family=Nunito+Sans:wght@400;600;700&display=swap">
<style>
  :root {
    --backdrop: #d9d5ce;
    --card-frost: #ecebe7;
    --card-edge: #f7f6f3;
    --brand-blue: #2f5f98;
    --brand-green: #3e9a52;
    --name-teal: #4593ad;
    --role-grey: #7b7d80;
    --band-blue-top: #3f73a0;
    --band-blue-bottom: #3468a0;
    --band-text: #dfe7ef;
    --emblem-fill: #c9d3da;
  }
  * { margin: 0; padding: 0; box-sizing: border-box; }
  html, body {
    width: 1200px;
    height: 1047px;
    overflow: hidden;
    background: var(--backdrop);
  }
  .business-card {
    position: absolute;
    left: 151px;
    top: 291px;
    width: 945px;
    height: 514px;
    border-radius: 22px;
    background: var(--card-frost);
    border: 2px solid var(--card-edge);
    overflow: hidden;
    font-family: "Nunito Sans", Arial, sans-serif;
  }
  .contact-band {
    position: absolute;
    left: 0;
    right: 0;
    top: 295px;
    bottom: 0;
    background: linear-gradient(180deg, var(--band-blue-top), var(--band-blue-bottom));
  }
  .company-name {
    position: absolute;
    left: 58px;
    top: 40px;
    font-family: "Archivo", Arial, sans-serif;
    font-weight: 700;
    color: var(--brand-blue);
    line-height: 1;
  }
  .company-name .company-main {
    display: block;
    font-size: 30px;
    letter-spacing: -0.5px;
  }
  .company-name .company-sub {
    display: block;
    margin-top: 5px;
    margin-left: 62px;
    font-size: 19px;
    letter-spacing: 7px;
    color: var(--brand-green);
  }
  .person {
    position: absolute;
    left: 58px;
    top: 206px;
  }
  .person-name {
    font-size: 27px;
    font-weight: 700;
    color: var(--name-teal);
    letter-spacing: 0.3px;
    line-height: 1.1;
  }
  .person-role {
    margin-top: 4px;
    font-size: 20px;
    color: var(--role-grey);
  }
  .social-row {
    position: absolute;
    left: 54px;
    top: 314px;
    display: flex;
    gap: 8px;
  }
  .social-dot {
    width: 24px;
    height: 24px;
    border-radius: 50%;
    background: var(--band-text);
  }
  .contact-list {
    position: absolute;
    left: 54px;
    top: 392px;
    list-style: none;
  }
  .contact-item {
    display: flex;
    align-items: center;
    height: 30px;
    font-size: 20px;
    color: var(--band-text);
    letter-spacing: 0.4px;
  }
  .contact-item svg {
    width: 20px;
    height: 20px;
    margin-right: 22px;
    flex: none;
  }
  .brand-emblem {
    position: absolute;
    left: 421px;
    top: 9px;
    width: 500px;
    height: 500px;
    border-radius: 50%;
    background: var(--emblem-fill);
  }
</style>
</head>
<body>
  <div class="business-card">
    <div class="contact-band"></div>

    <div class="company-name">
      <span class="company-main">KESTON FIELDWORKS</span>
      <span class="company-sub">SERVICES</span>
    </div>

    <div class="person">
      <div class="person-name">DEAN HARLOW</div>
      <div class="person-role">Director</div>
    </div>

    <div class="social-row" aria-label="Social media links">
      <span class="social-dot"></span>
      <span class="social-dot"></span>
      <span class="social-dot"></span>
    </div>

    <ul class="contact-list">
      <li class="contact-item">
        <svg viewBox="0 0 20 20" aria-hidden="true"><path d="M5 2c1 0 2 3 2 4s-1.5 1.5-1 2.5 3 4 4.5 4.5 1.5-1 2.5-1 4 1 4 2-1.5 3-3 3C8 17 3 12 2 6c0-1.5 2-4 3-4z" fill="none" stroke="var(--band-text)" stroke-width="1.6"/></svg>
        <span>0487305526</span>
      </li>
      <li class="contact-item">
        <svg viewBox="0 0 20 20" aria-hidden="true"><rect x="2" y="4.5" width="16" height="11" fill="none" stroke="var(--band-text)" stroke-width="1.6"/><path d="M2 4.5l8 6 8-6" fill="none" stroke="var(--band-text)" stroke-width="1.6"/></svg>
        <span>dean@kolvat.biz</span>
      </li>
      <li class="contact-item">
        <svg viewBox="0 0 20 20" aria-hidden="true"><circle cx="10" cy="10" r="8" fill="none" stroke="var(--band-text)" stroke-width="1.5"/><ellipse cx="10" cy="10" rx="3.5" ry="8" fill="none" stroke="var(--band-text)" stroke-width="1.3"/><path d="M2 10h16M3.5 6h13M3.5 14h13" stroke="var(--band-text)" stroke-width="1.2"/></svg>
        <span>www.kestonfieldworks.com</span>
      </li>
    </ul>

    <div class="brand-emblem" role="img" aria-label="Place for the Keston Fieldworks company emblem"></div>
  </div>
</body>
</html>
```